A-Stand Directional Sign Design

Objective:
We need a professional graphic design for an A-Stand sign that will guide customers arriving in our parking lot to our office. The design should be visually clear, welcoming, and aligned with our brand identity.
REQUIREMENTS:
Two versions of the design:
- One with an arrow pointing left
- One with an arrow pointing right
(This allows us to place the A-Stand anywhere and flip the graphic as needed.)
DIMENSIONS:
- Viewable Area: 30" x 40"
BRAND ALIGNMENT:
- Colors, fonts, and overall style should match our website: www.glidemarrow.com
- Clean, modern, and professional look consistent with our aviation/tourism brand
CONTENT:
- Clear directional arrow (left or right depending on version)
- Text: “Office Entrance” or similar concise wording (designers may propose alternatives if they improve clarity)
READABILITY:
- Bold, high-contrast design for visibility from a distance
- Simple layout that avoids clutter
DELIVERABLES:
- Final artwork in print-ready format (PDF preferred)
- Two versions: Arrow Left and Arrow Right
DESIGN GOAL:
Ensure customers can easily find our office upon arrival, while reinforcing glideMARROW’s professional and welcoming brand image.
Target Market(s)
Tourism
Look and feel

```html
<!DOCTYPE html>
<html lang="en">
<head>
<meta charset="utf-8">
<title>glideMARROW – Office Entrance A-Stand Signs</title>
<link rel="stylesheet" href="https://fonts.googleapis.com/css2?family=Montserrat:wght@600;700&display=swap">
<style>
  :root {
    --page: #ffffff;
    --panel: #ffffff;
    --brand-deep: #004ab8;
    --brand-bright: #0a66f5;
    --brand-text: #0a72d6;
    --white: #ffffff;
    --chevron-far: #5f88cc;
    --chevron-mid: #bccbe3;
    --chevron-near: #ebebeb;
  }
  * { margin: 0; padding: 0; box-sizing: border-box; }
  html, body {
    width: 1200px; height: 811px; overflow: hidden;
    background: var(--page);
    font-family: "Montserrat", sans-serif;
  }
  .canvas { position: relative; width: 1200px; height: 811px; }
  .sign {
    position: absolute; top: 60px;
    width: 519px; height: 691px;
    background: var(--panel);
    box-shadow: 0 18px 40px rgba(0,0,0,0.22);
    overflow: hidden;
  }
  .sign--right { left: 53px; }
  .sign--left { left: 611px; }
  .sign__wave { position: absolute; inset: 0; width: 100%; height: 100%; }
  .brand {
    position: absolute; top: 34px; left: 0; width: 100%;
    display: flex; flex-direction: column; align-items: center; gap: 14px;
  }
  .brand__dot {
    width: 54px; height: 54px; border-radius: 50%;
    background: var(--brand-text);
  }
  .brand__name {
    font-weight: 600; font-size: 34px; letter-spacing: 1px;
    color: var(--brand-text);
  }
  .label {
    position: absolute; left: 59px; top: 319px;
    width: 401px; height: 75px;
    border: 2px solid var(--white);
    display: flex; align-items: center; justify-content: center;
    color: var(--white); font-weight: 700; font-size: 35px; letter-spacing: 0.5px;
  }
  .arrows { position: absolute; left: 0; top: 0; width: 519px; height: 691px; }
  .url {
    position: absolute; left: 0; width: 100%; top: 617px;
    text-align: center; color: var(--white);
    font-weight: 700; font-size: 15px; letter-spacing: 1px;
  }
</style>
</head>
<body>
<main class="canvas">

  <section class="sign sign--right" aria-label="Office entrance sign, arrow pointing right">
    <svg class="sign__wave" viewBox="0 0 519 691" aria-hidden="true">
      <path fill="var(--brand-bright)" d="M0 286 C110 205 230 180 334 182 C420 183 480 198 519 211 L519 691 L0 691 Z"/>
      <path fill="var(--brand-deep)" d="M0 300 C110 222 230 190 334 188 C420 188 480 200 519 213 L519 691 L0 691 Z"/>
    </svg>
    <div class="brand"><span class="brand__dot"></span><span class="brand__name">glideMARROW</span></div>
    <div class="label">OFFICE ENTRANCE</div>
    <svg class="arrows" viewBox="0 0 519 691" aria-hidden="true" fill="none" stroke-width="26" stroke-linecap="round" stroke-linejoin="round">
      <polyline stroke="var(--chevron-far)" points="138,455 185,508 138,559"/>
      <polyline stroke="var(--chevron-mid)" points="234,455 281,508 234,559"/>
      <polyline stroke="var(--chevron-near)" points="330,455 377,508 330,559"/>
    </svg>
    <p class="url">WWW.GLIDEMARROW.COM</p>
  </section>

  <section class="sign sign--left" aria-label="Office entrance sign, arrow pointing left">
    <svg class="sign__wave" viewBox="0 0 519 691" aria-hidden="true">
      <path fill="var(--brand-bright)" d="M0 286 C110 205 230 180 334 182 C420 183 480 198 519 211 L519 691 L0 691 Z"/>
      <path fill="var(--brand-deep)" d="M0 300 C110 222 230 190 334 188 C420 188 480 200 519 213 L519 691 L0 691 Z"/>
    </svg>
    <div class="brand"><span class="brand__dot"></span><span class="brand__name">glideMARROW</span></div>
    <div class="label">OFFICE ENTRANCE</div>
    <svg class="arrows" viewBox="0 0 519 691" aria-hidden="true" fill="none" stroke-width="26" stroke-linecap="round" stroke-linejoin="round">
      <g transform="translate(519 0) scale(-1 1)">
        <polyline stroke="var(--chevron-far)" points="138,455 185,508 138,559"/>
        <polyline stroke="var(--chevron-mid)" points="234,455 281,508 234,559"/>
        <polyline stroke="var(--chevron-near)" points="330,455 377,508 330,559"/>
      </g>
    </svg>
    <p class="url">WWW.GLIDEMARROW.COM</p>
  </section>

</main>
</body>
</html>
```